We are a local Communty Pharmacy wishing to promote and market a specialised Pharmaceutical Service

We would like a design that is professional and enticing ( according to the brief In attached files)
We wish to Market Compounding Pharmacy as a specialist side of our business.
We have the expertise a purpose built preparation laboratory.
The main purpose is an Internet presence that entices prospective patients to contact or visit our physical store.

Target Market(s)

Patients Medicos and Veterinary clients

Industry/Entity Type

Pharmacy

Coding

Coded - Design and coding required

Number of Pages Required

1 page

Requirements
Must have
• Clear friendly image
Nice to have
• soft enticing feel
Should not have
• No crass loud unprofessional elements

```html
<!DOCTYPE html>
<html lang="en">
<head>
<meta charset="utf-8">
<title>Compounding Pharmacy</title>
<link href="https://fonts.googleapis.com/css2?family=Open+Sans:wght@400;600;700&display=swap" rel="stylesheet">
<style>
:root{
  --orange:#f28c1c;
  --navy:#1f4f7a;
  --ink:#3a3f45;
  --muted:#8a9099;
  --line:#e3e5e8;
  --hero-a:#f4f4f4;
  --hero-b:#dcdcdc;
  --green:#a9c84a;
  --blue:#5cbfe6;
  --amber:#f2a93b;
  --violet:#b48fd2;
  --footer:#2f353c;
  --footer-text:#aab0b7;
}
*{box-sizing:border-box;margin:0;padding:0}
html,body{width:705px;height:1200px;overflow:hidden}
body{font-family:"Open Sans",Arial,sans-serif;color:var(--ink);background:#fff;font-size:8px;line-height:1.5}
.site-header{height:50px;display:flex;align-items:center;justify-content:space-between;padding:0 30px;border-bottom:1px solid var(--line)}
.brand{font-weight:600;font-size:12px;color:var(--navy);letter-spacing:.3px}
.main-nav{display:flex;gap:30px}
.main-nav a{font-size:8px;font-weight:600;color:var(--ink);text-decoration:none;letter-spacing:.5px}
.main-nav a.active{color:var(--orange)}
.hero{position:relative;height:285px;background:linear-gradient(180deg,var(--hero-a),var(--hero-b))}
.hero-copy{position:absolute;left:70px;top:95px;width:260px}
.hero-title{font-size:18px;font-weight:700;color:var(--navy);letter-spacing:.3px}
.hero-title span{color:var(--orange)}
.hero-text{margin:8px 0 14px;color:var(--muted);font-size:7.5px}
.btn{display:inline-block;background:var(--orange);color:#fff;font-size:7px;font-weight:600;padding:7px 14px;letter-spacing:.5px;text-transform:uppercase}
.hero-media{position:absolute;right:75px;top:45px;width:250px;height:200px;border-radius:8px;background:radial-gradient(ellipse at 50% 55%,#f3b35a 0%,#e98d2a 40%,rgba(220,220,220,0) 72%)}
.hero-arrow{position:absolute;top:130px;width:18px;height:18px;border-radius:50%;background:#9a9ea3;display:flex;align-items:center;justify-content:center}
.hero-arrow.prev{left:8px}.hero-arrow.next{right:8px}
.features{display:flex;margin:12px 30px 0;height:135px}
.feature{flex:1;color:#fff;text-align:center;padding:20px 12px 0}
.feature.green{background:var(--green)}.feature.blue{background:var(--blue)}.feature.amber{background:var(--amber)}.feature.violet{background:var(--violet)}
.feature-icon{width:34px;height:34px;border-radius:50%;border:1.5px solid rgba(255,255,255,.85);margin:0 auto 10px;display:flex;align-items:center;justify-content:center}
.feature h3{font-size:9px;font-weight:600;margin-bottom:4px}
.feature p{font-size:6.5px;opacity:.9}
.welcome{display:flex;gap:22px;margin:18px 30px 0;height:190px}
.welcome-main{flex:1}
.section-title{font-size:10px;font-weight:700;color:var(--navy);text-transform:uppercase;padding-bottom:6px;border-bottom:1px solid var(--line);margin-bottom:12px}
.welcome-body{display:flex;gap:12px}
.welcome-video{position:relative;width:135px;height:95px;background:linear-gradient(135deg,#d5e6f3,#9fc3de);flex:none}
.play{position:absolute;left:50%;top:50%;width:24px;height:24px;margin:-12px 0 0 -12px;border-radius:50%;background:rgba(255,255,255,.85);display:flex;align-items:center;justify-content:center}
.welcome-text p{font-size:6.5px;color:var(--muted);margin-bottom:6px}
.read-more{font-size:7px;font-weight:700;color:var(--navy);display:flex;align-items:center;gap:5px}
.read-more i{display:inline-block;width:7px;height:7px;border-radius:50%;background:var(--orange)}
.testimonials{width:175px}
.testimonials .section-title{text-transform:none;font-weight:600}
.testimonials .section-title span{color:var(--orange)}
.quote{border:1px solid var(--line);padding:10px;font-size:6.5px;color:var(--muted)}
.author{display:flex;align-items:center;gap:8px;margin-top:10px;font-size:7px}
.avatar{width:26px;height:26px;border-radius:50%;background:linear-gradient(135deg,#c9ccd1,#9aa0a8)}
.author b{color:var(--orange);font-weight:600}
.purpose{display:flex;margin:20px 30px 0;height:50px;background:#f2f3f4}
.purpose-copy{flex:1;padding:8px 18px}
.purpose-copy h3{font-size:10px;font-weight:600;color:var(--navy);margin-bottom:2px}
.purpose-copy p{font-size:6.5px;color:var(--muted)}
.purpose-cta{width:180px;background:var(--orange);clip-path:polygon(22% 0,100% 0,100% 100%,0 100%);display:flex;align-items:center;justify-content:center;padding-left:30px}
.purpose-cta span{background:var(--navy);color:#fff;font-size:7px;font-weight:600;padding:6px 12px}
.products{margin:40px 30px 0;height:190px}
.products h2{text-align:center;font-size:14px;font-weight:600;color:var(--navy);letter-spacing:.5px;margin-bottom:14px}
.product-grid{display:flex;gap:14px}
.product{flex:1;border:1px solid var(--line)}
.product-media{height:110px}
.product-media.p1{background:linear-gradient(135deg,#e8eaed,#c8ccd2)}
.product-media.p2{background:linear-gradient(135deg,#f5e3de,#d9534f)}
.product-media.p3{background:linear-gradient(135deg,#e9eef5,#2f5d8a)}
.product-media.p4{background:linear-gradient(135deg,#f3ece0,#e9a64a)}
.product p{font-size:6.5px;font-weight:600;text-align:center;padding:6px 0;color:var(--ink)}
.site-footer{display:flex;gap:26px;height:153px;margin-top:25px;background:var(--footer);padding:18px 30px;color:var(--footer-text)}
.footer-col{flex:1}
.footer-col h4{font-size:8px;font-weight:600;color:#fff;text-transform:uppercase;margin-bottom:10px}
.map{height:72px;background:linear-gradient(135deg,#e8e8e6,#cfd3d6)}
.footer-col p{font-size:6.5px;margin-bottom:10px}
.field{height:18px;border:1px solid #4a5159;margin-bottom:8px;font-size:6.5px;padding:3px 6px;color:#7d848c}
.subscribe{display:flex;gap:6px}
.subscribe .field{flex:1}
.subscribe span{background:var(--orange);color:#fff;font-size:6.5px;font-weight:600;height:18px;padding:3px 10px}
.contact-row{display:flex;gap:8px;align-items:flex-start;font-size:6.5px;margin-bottom:9px}
.contact-row svg{flex:none;margin-top:1px}
.bottom-bar{height:32px;background:var(--orange);display:flex;align-items:center;justify-content:space-between;padding:0 30px;color:#fff;font-size:6.5px}
.social{display:flex;gap:5px}
.social i{width:12px;height:12px;border-radius:50%;background:rgba(255,255,255,.35);display:block}
</style>
</head>
<body>
<header class="site-header">
  <div class="brand">Compounding Pharmacy</div>
  <nav class="main-nav">
    <a class="active" href="#">HOME</a><a href="#">ABOUT US</a><a href="#">LOCATIONS</a><a href="#">THINGS</a><a href="#">CONTACT</a>
  </nav>
</header>

<section class="hero">
  <div class="hero-copy">
    <h1 class="hero-title">COMPOUNDING <span>PHARMACY</span></h1>
    <p class="hero-text">Medicines prepared for you in our own laboratory, matched to the dose, strength and form your doctor or vet prescribes for each patient.</p>
    <span class="btn">Read more about</span>
  </div>
  <div class="hero-media" role="img" aria-label="Orange prescription bottles with white tablets"></div>
  <span class="hero-arrow prev"><svg width="6" height="8" viewBox="0 0 6 8"><path d="M5 1 2 4l3 3" stroke="#fff" stroke-width="1.4" fill="none"/></svg></span>
  <span class="hero-arrow next"><svg width="6" height="8" viewBox="0 0 6 8"><path d="M1 1l3 3-3 3" stroke="#fff" stroke-width="1.4" fill="none"/></svg></span>
</section>

<section class="features">
  <div class="feature green">
    <div class="feature-icon"><svg width="14" height="14" viewBox="0 0 14 14"><path d="M7 13V6M7 6C7 3 4 2 2 2c0 3 2 4 5 4zm0 0c0-3 3-4 5-4 0 3-2 4-5 4" stroke="#fff" stroke-width="1.2" fill="none"/></svg></div>
    <h3>We are a compounding</h3><p>Custom preparations made on site by trained pharmacists.</p>
  </div>
  <div class="feature blue">
    <div class="feature-icon"><svg width="14" height="14" viewBox="0 0 14 14"><circle cx="7" cy="5" r="2.5" stroke="#fff" stroke-width="1.2" fill="none"/><path d="M2.5 13c0-3 2-4.5 4.5-4.5s4.5 1.5 4.5 4.5" stroke="#fff" stroke-width="1.2" fill="none"/></svg></div>
    <h3>Where we are</h3><p>Visit our local store and purpose built laboratory.</p>
  </div>
  <div class="feature amber">
    <div class="feature-icon"><svg width="14" height="14" viewBox="0 0 14 14"><circle cx="3" cy="7" r="1.6" fill="#fff"/><circle cx="11" cy="3" r="1.6" fill="#fff"/><circle cx="11" cy="11" r="1.6" fill="#fff"/><path d="M3 7l8-4M3 7l8 4" stroke="#fff" stroke-width="1"/></svg></div>
    <h3>What we are here</h3><p>Serving patients, medicos and veterinary clients.</p>
  </div>
  <div class="feature violet">
    <div class="feature-icon"><svg width="14" height="14" viewBox="0 0 14 14"><rect x="1.5" y="3" width="11" height="8" stroke="#fff" stroke-width="1.2" fill="none"/><path d="M1.5 3 7 8l5.5-5" stroke="#fff" stroke-width="1.2" fill="none"/></svg></div>
    <h3>How you can visit contact</h3><p>Call, email or drop in to talk with our team.</p>
  </div>
</section>

<section class="welcome">
  <div class="welcome-main">
    <h2 class="section-title">Welcome to Compounding Pharmacy</h2>
    <div class="welcome-body">
      <div class="welcome-video" role="img" aria-label="Pharmacist preparing medicine, video preview">
        <span class="play"><svg width="8" height="9" viewBox="0 0 8 9"><path d="M1 0.5v8l6.5-4z" fill="var(--orange)"/></svg></span>
      </div>
      <div class="welcome-text">
        <p>Our pharmacy has served the local community for many years. We now offer a specialised compounding service, preparing medicines that are not available off the shelf.</p>
        <p>Each preparation is made to order in our purpose built laboratory, with care for allergies, flavours and dosage forms that suit the patient best.</p>
        <span class="read-more">READ MORE <i></i></span>
      </div>
    </div>
  </div>
  <aside class="testimonials">
    <h2 class="section-title">Customer <span>Testimonials</span></h2>
    <div class="quote">The team prepared a gentle liquid form of my medicine when tablets were too hard to take. Friendly, clear advice and always ready on time.</div>
    <div class="author"><span class="avatar" role="img" aria-label="Customer portrait"></span><span><b>Nora Kelby</b> - manager</span></div>
  </aside>
</section>

<section class="purpose">
  <div class="purpose-copy">
    <h3>PURPOSE</h3>
    <p>To provide an awareness of where medicine can be tailored, and the special services of Compounding Pharmacy, so patients are enticed to contact and visit our store.</p>
  </div>
  <div class="purpose-cta"><span>SIGN UP FREE</span></div>
</section>

<section class="products">
  <h2>FEATURED PRODUCTS &amp; SERVICES</h2>
  <div class="product-grid">
    <div class="product"><div class="product-media p1" role="img" aria-label="Compounding tools and capsules"></div><p>DUIS AUTE IRURE DOLOR</p></div>
    <div class="product"><div class="product-media p2" role="img" aria-label="Red and white capsules"></div><p>DUIS AUTE IRURE DOLOR</p></div>
    <div class="product"><div class="product-media p3" role="img" aria-label="Blue medicine jar"></div><p>DUIS AUTE IRURE DOLOR</p></div>
    <div class="product"><div class="product-media p4" role="img" aria-label="Amber medicine bottles"></div><p>DUIS AUTE IRURE DOLOR</p></div>
  </div>
</section>

<footer class="site-footer">
  <div class="footer-col">
    <h4>Our Location</h4>
    <div class="map" role="img" aria-label="Street map showing the pharmacy location"></div>
  </div>
  <div class="footer-col">
    <h4>Sign up for newsletter</h4>
    <p>Subscribe to our monthly newsletter and keep up to date with new services.</p>
    <div class="field">Enter Name</div>
    <div class="subscribe"><div class="field">Enter Email</div><span>SUBSCRIBE</span></div>
  </div>
  <div class="footer-col">
    <h4>Contact Us</h4>
    <div class="contact-row"><svg width="9" height="11" viewBox="0 0 9 11"><path d="M4.5 10.5S1 6.5 1 4.2a3.5 3.5 0 0 1 7 0C8 6.5 4.5 10.5 4.5 10.5z" fill="#fff"/><circle cx="4.5" cy="4.2" r="1.2" fill="var(--footer)"/></svg><span>Compounding Pharmacy<br>48 Harbour Lane, Eastfield 2041</span></div>
    <div class="contact-row"><svg width="9" height="9" viewBox="0 0 9 9"><path d="M2 .5 3.5 2.8 2.6 4a5 5 0 0 0 2.4 2.4l1.2-.9L8.5 7 7.6 8.5C4 8.3.7 5 .5 1.4z" fill="#fff"/></svg><span>+1 555 0142 2288</span></div>
    <div class="contact-row"><svg width="10" height="8" viewBox="0 0 10 8"><rect x=".5" y=".5" width="9" height="7" fill="#fff"/><path d="M.5.5 5 4.5 9.5.5" stroke="var(--footer)" fill="none"/></svg><span>care@fernhillchemist.example</span></div>
  </div>
</footer>
<div class="bottom-bar">
  <span>2024 © Copyrights Compounding Pharmacy</span>
  <div class="social"><i></i><i></i><i></i><i></i></div>
</div>
</body>
</html>
```